Event Website Design

We need a new website design for an events driven website. The domain for this site is http://brackmoorhalls.co.uk. The site is up and running but needs a new fresh, modern look.
I've attached a Balamiq Mockup for the layout of the home page. Also attached is a png of the logo.
Key colours for the site are 0f7e6a, 35bde, d57835 & 373737.
Font to use is Proxima Nova
Width of the site should be 1200px
The design should be contemporary with minimal clutter.
Websites to references are…
http://vorpin.london/
http://www.darvushall.co.uk/
These are just guidelines, please feel free to use you own creative judgment.
The selected design file needs to be supplied as an editable PSD.
Reason: I've submitted 5 designs to the client, who will select the one they want. I will then choose that design. So please be patient as I'm waiting for a decision from my client.
Industry/Entity Type
Events
Number of Pages Required
1 page
Look and feel
Each slider illustrates characteristics of the customer's brand and the style your logo design should communicate.

```html
<!DOCTYPE html>
<html lang="en">
<head>
<meta charset="utf-8">
<title>Brackmoor Halls – Entertainment &amp; Sporting Center</title>
<link rel="stylesheet" href="https://fonts.googleapis.com/css2?family=Figtree:wght@300;400;600;700;800&display=swap">
<style>
:root{
  --teal:#0f7e6a;
  --teal-soft:#2a9a83;
  --orange:#d57835;
  --charcoal:#373737;
  --blue:#2f6fb8;
  --ink:#2b2b2b;
  --muted:#8a8a8a;
  --line:#e2e2e2;
  --panel:#f4f4f4;
  --white:#ffffff;
}
*{box-sizing:border-box;margin:0;padding:0}
html,body{width:1200px;height:2459px;overflow:hidden}
body{position:relative;font-family:"Figtree",Arial,sans-serif;color:var(--ink);background:var(--white)}
a{color:inherit;text-decoration:none}
.section{position:absolute;left:0;width:1200px}
.wrap{position:absolute;left:131px;width:938px}
.btn{display:inline-flex;align-items:center;justify-content:center;border-radius:18px;color:var(--white);font-weight:700;font-size:12px;letter-spacing:.5px}
.btn-more{background:var(--teal)}
.btn-book{background:var(--orange)}

/* header */
.site-header{top:0;height:164px;border-top:4px solid var(--teal)}
.brand{position:absolute;left:131px;top:52px;display:flex;align-items:center;gap:20px}
.brand-mark{width:20px;height:20px;background:var(--teal)}
.brand-name{font-weight:800;font-size:26px;line-height:1.05;color:var(--charcoal);letter-spacing:.5px}
.brand-tag{position:absolute;left:322px;top:88px;font-size:11.5px;line-height:19px;color:var(--teal);font-weight:600;width:140px}
.utility{position:absolute;right:131px;top:42px;display:flex;font-size:11.5px;color:#555}
.utility a{display:flex;align-items:center;gap:6px;padding:0 12px;border-left:1px solid var(--line)}
.utility a:first-child{border-left:none}
.utility svg{width:11px;height:11px}
.box-office{position:absolute;left:517px;top:88px;display:flex;align-items:center;gap:12px;font-size:19px;color:#666}
.box-office strong{color:var(--charcoal);font-weight:700}
.phone-dot{width:34px;height:34px;border-radius:50%;background:var(--orange);display:flex;align-items:center;justify-content:center}
.social{position:absolute;left:782px;top:88px;display:flex;gap:4px}
.social span{width:33px;height:33px;border:2px solid var(--blue);border-radius:50%;display:flex;align-items:center;justify-content:center}
.search{position:absolute;left:905px;top:91px;width:164px;height:27px;border:1px solid #d4d4d4;border-radius:14px;font-size:11px;color:#aaa;padding:0 12px;display:flex;align-items:center;justify-content:space-between}

/* nav */
.main-nav{top:164px;height:52px;background:var(--charcoal)}
.main-nav ul{list-style:none;position:absolute;left:143px;right:131px;top:0;height:52px;display:flex;justify-content:space-between;align-items:center}
.main-nav li{color:var(--white);font-size:11.5px;font-weight:600;letter-spacing:.3px}

/* hero */
.hero{top:216px;height:514px;background:radial-gradient(ellipse at 55% 45%,#3a4f9c 0%,#2a2a5a 30%,#3a1d22 60%,#1d1514 100%)}
.hero-title{position:absolute;left:131px;top:236px;font-size:37px;font-weight:300;color:var(--white);letter-spacing:.5px}
.hero-title b{font-weight:800}
.hero-date{position:absolute;left:131px;top:292px;display:flex;align-items:center;gap:12px;color:var(--white);font-size:14px;font-weight:600}
.date-dot{width:40px;height:40px;border-radius:50%;background:var(--orange);display:flex;align-items:center;justify-content:center}
.hero-copy{position:absolute;left:131px;top:345px;width:500px;color:var(--white);font-size:16px;line-height:24px}
.hero-actions{position:absolute;left:885px;top:378px;display:flex;gap:7px}
.hero-actions .btn{width:87px;height:37px}
.hero-dots{position:absolute;left:557px;top:448px;display:flex;gap:12px}
.hero-dots i{width:12px;height:12px;border-radius:50%;border:1.5px solid var(--white)}
.hero-dots i:first-child{background:var(--white)}

/* events */
.events{top:730px;height:357px}
.carousel-arrow{position:absolute;top:82px;width:44px;height:44px;border-radius:50%;background:#e3e3e3;display:flex;align-items:center;justify-content:center}
.events-grid{top:32px;display:grid;grid-template-columns:repeat(4,228px);gap:8px}
.event-card{text-align:center;padding-bottom:16px;border-bottom:2px dotted #cfcfcf;margin:0 20px}
.event-card .thumb{height:143px;margin:0 -20px}
.event-title{margin-top:20px;font-size:14px;font-weight:600;color:var(--charcoal)}
.event-date{margin-top:7px;font-size:10.5px;color:var(--orange);font-weight:600}
.event-actions{margin-top:12px;display:flex;justify-content:center;gap:4px}
.event-actions .btn{width:80px;height:34px}

/* news */
.news{top:1087px;height:381px;background:linear-gradient(180deg,#262626 0%,#1c1c1c 100%)}
.news-heading{position:absolute;left:131px;top:58px;font-size:25px;font-weight:300;color:var(--white)}
.news-heading b{font-weight:800}
.news-grid{top:128px;display:grid;grid-template-columns:repeat(3,292px);gap:31px}
.story{position:relative;background:var(--white);border-radius:3px;height:171px;padding:22px 20px}
.story::after{content:"";position:absolute;left:20px;bottom:-16px;border-top:16px solid var(--white);border-right:16px solid transparent}
.story h3{font-size:13px;font-weight:600;color:var(--charcoal)}
.story p{margin-top:9px;font-size:10.5px;line-height:18px;color:#777}
.story .btn{margin-top:13px;width:82px;height:34px}

/* features */
.features{top:1468px;height:467px;background:var(--panel)}
.features-grid{top:57px;display:grid;grid-template-columns:repeat(3,292px);gap:31px}
.feature{background:var(--white);border:1px solid var(--line);height:345px;padding:8px;text-align:center;position:relative}
.feature .thumb{height:159px}
.feature-icon{position:absolute;left:50%;top:128px;margin-left:-37px;width:74px;height:74px;border-radius:50%;background:var(--teal);border:3px solid var(--white);display:flex;align-items:center;justify-content:center}
.feature h3{margin-top:58px;font-size:13px;font-weight:600;color:var(--charcoal)}
.feature p{margin-top:9px;font-size:10.5px;line-height:18px;color:#777;padding:0 20px}
.feature .btn{margin-top:12px;width:82px;height:34px}

/* sports band */
.sports{top:1935px;height:274px;background:linear-gradient(90deg,#0f7e6a 0%,#1a8a74 50%,#0f7e6a 100%);text-align:center;color:var(--white)}
.sports h2{margin-top:95px;font-size:37px;font-weight:300;letter-spacing:.5px}
.sports h2 b{font-weight:800}
.sports a{display:block;margin-top:12px;font-size:13px;font-weight:600}

/* footer */
.site-footer{top:2209px;height:250px}
.footer-logo{position:absolute;left:131px;top:55px;width:223px;height:124px;border:1px solid var(--line);display:flex;align-items:center;justify-content:center;gap:12px}
.footer-logo .brand-mark{width:16px;height:16px}
.footer-logo .brand-name{font-size:22px}
.copyright{position:absolute;left:131px;top:194px;font-size:10.5px;color:#666}
.divider{position:absolute;top:55px;width:1px;height:140px;background:var(--line)}
.footer-col{position:absolute;top:55px}
.footer-col h4{font-size:12.5px;font-weight:600;color:var(--charcoal);letter-spacing:.4px}
.footer-col ul{list-style:none;margin-top:14px}
.footer-col li{font-size:11px;color:#666;line-height:24px}
.footer-col.extra ul{margin-top:32px}
.footer-col.extra li{line-height:19px}
</style>
</head>
<body>

<header class="section site-header">
  <div class="brand"><span class="brand-mark"></span><span class="brand-name">BRACKMOOR<br>HALLS</span></div>
  <p class="brand-tag">Wessex's Premier Entertainment &amp; Sporting Center</p>
  <nav class="utility">
    <a href="#"><svg viewBox="0 0 12 12"><rect x="1" y="4" width="10" height="7" fill="#555"/><rect x="0" y="2" width="12" height="3" fill="#555"/></svg>Gift Voucher</a>
    <a href="#"><svg viewBox="0 0 12 12"><rect x="1" y="2.5" width="10" height="7" fill="none" stroke="#555"/><path d="M1 2.5l5 4 5-4" fill="none" stroke="#555"/></svg>Join Our Mailing List</a>
    <a href="#"><svg viewBox="0 0 12 12"><path d="M2 10l1-3 6-6 2 2-6 6z" fill="#555"/></svg>My Account</a>
    <a href="#"><svg viewBox="0 0 12 12"><path d="M1 1h5l5 5-5 5-5-5z" fill="#555"/></svg>Basket</a>
    <a href="#"><svg viewBox="0 0 12 12"><rect x="1" y="1" width="10" height="10" fill="none" stroke="#555"/><path d="M4 8l5-5" stroke="#555"/></svg>Register</a>
  </nav>
  <div class="box-office">
    <span class="phone-dot"><svg width="14" height="14" viewBox="0 0 14 14"><path d="M3 1l3 3-1.5 1.5a8 8 0 0 0 4 4L10 8l3 3-2 2C6 13 1 8 1 3z" fill="#fff"/></svg></span>
    <span>Box Office : <strong>01632 960 482</strong></span>
  </div>
  <div class="social">
    <span></span><span></span>
    <span><svg width="13" height="13" viewBox="0 0 13 13"><rect x="1" y="2" width="11" height="10" fill="none" stroke="#2f6fb8" stroke-width="1.4"/><path d="M1 5h11M4 0.5v3M9 0.5v3" stroke="#2f6fb8" stroke-width="1.4"/></svg></span>
  </div>
  <div class="search">Search... <svg width="11" height="11" viewBox="0 0 11 11"><circle cx="4.5" cy="4.5" r="3.5" fill="none" stroke="#aaa" stroke-width="1.4"/><path d="M7 7l3 3" stroke="#aaa" stroke-width="1.4"/></svg></div>
</header>

<nav class="section main-nav">
  <ul>
    <li>WHAT'S ON</li><li>CONFERENCING &amp; EVENTS</li><li>SPORTS &amp; LEISURE</li><li>LANTERN THEATRE</li><li>PLAN YOUR VISIT</li><li>NEWS</li><li>DISCOVER MORE</li><li>CONTACT US</li>
  </ul>
</nav>

<section class="section hero" role="img" aria-label="Stage photo of cabaret dancers in feathered costumes">
  <h1 class="hero-title">ENTERTAINMENT <b>&amp; SPORTING</b></h1>
  <div class="hero-date">
    <span class="date-dot"><svg width="16" height="16" viewBox="0 0 16 16"><rect x="2" y="3" width="12" height="11" fill="none" stroke="#fff" stroke-width="1.5"/><path d="M2 7h12M5 1v4M11 1v4" stroke="#fff" stroke-width="1.5"/></svg></span>
    MONDAY,26 DECEMBER,2016
  </div>
  <p class="hero-copy">Sed do eiusmod tempor incididunt ut labore et dolore magna aliqua. enim ad minim veniam, quis nostrud exercitation ullamco laboris nisi aliquip ex ea commodo consequat...</p>
  <div class="hero-actions"><a class="btn btn-more" href="#">MORE</a><a class="btn btn-book" href="#">BOOK</a></div>
  <div class="hero-dots"><i></i><i></i><i></i><i></i></div>
</section>

<section class="section events">
  <span class="carousel-arrow" style="left:57px"><svg width="10" height="12" viewBox="0 0 10 12"><path d="M7 1L2 6l5 5" fill="none" stroke="#fff" stroke-width="2"/></svg></span>
  <span class="carousel-arrow" style="left:1098px"><svg width="10" height="12" viewBox="0 0 10 12"><path d="M3 1l5 5-5 5" fill="none" stroke="#fff" stroke-width="2"/></svg></span>
  <div class="wrap events-grid">
    <article class="event-card">
      <div class="thumb" role="img" aria-label="Ballet dancers on stage" style="background:linear-gradient(135deg,#5a3a3a,#c9b3a5 55%,#6b4a44)"></div>
      <h3 class="event-title">EIUSMOD TEMPOR</h3>
      <p class="event-date">TUESDAY,26 DECEMBER,2016</p>
      <div class="event-actions"><a class="btn btn-more" href="#">MORE</a><a class="btn btn-book" href="#">BOOK</a></div>
    </article>
    <article class="event-card">
      <div class="thumb" role="img" aria-label="Performer in white costume with fan on a lilac stage" style="background:linear-gradient(135deg,#c58ad8,#e6d4ef 55%,#b873cf)"></div>
      <h3 class="event-title">EIUSMOD TEMPOR</h3>
      <p class="event-date">TUESDAY,26 DECEMBER,2016</p>
      <div class="event-actions"><a class="btn btn-more" href="#">MORE</a><a class="btn btn-book" href="#">BOOK</a></div>
    </article>
    <article class="event-card">
      <div class="thumb" role="img" aria-label="Theatre cast in period costume" style="background:linear-gradient(135deg,#3f5a4a,#b8b29a 55%,#4e6b5a)"></div>
      <h3 class="event-title">EIUSMOD TEMPOR</h3>
      <p class="event-date">TUESDAY,26 DECEMBER,2016</p>
      <div class="event-actions"><a class="btn btn-more" href="#">MORE</a><a class="btn btn-book" href="#">BOOK</a></div>
    </article>
    <article class="event-card">
      <div class="thumb" role="img" aria-label="Comedy show poster marked sold out" style="background:linear-gradient(135deg,#3aa9d9,#f0d24a 60%,#d94a3a)"></div>
      <h3 class="event-title">EIUSMOD TEMPOR</h3>
      <p class="event-date">TUESDAY,26 DECEMBER,2016</p>
      <div class="event-actions"><a class="btn btn-more" href="#">MORE</a><a class="btn btn-book" href="#">BOOK</a></div>
    </article>
  </div>
</section>

<section class="section news" role="img" aria-label="Dark city skyline at night behind news stories">
  <h2 class="news-heading">LATEST FROM <b>BRACKMOOR</b></h2>
  <div class="wrap news-grid">
    <article class="story">
      <h3>NEW STORY 1</h3>
      <p>Accusantium doloremque laudantium, totamed rem aperiam, eaque ipsa quae ab illo inventore veritatis et quasi architecto beatae vitae dicta...</p>
      <a class="btn btn-more" href="#">MORE</a>
    </article>
    <article class="story">
      <h3>NEW STORY 2</h3>
      <p>Accusantium doloremque laudantium, totamed rem aperiam, eaque ipsa quae ab illo inventore veritatis et quasi architecto beatae vitae dicta...</p>
      <a class="btn btn-more" href="#">MORE</a>
    </article>
    <article class="story">
      <h3>NEW STORY 3</h3>
      <p>Accusantium doloremque laudantium, totamed rem aperiam, eaque ipsa quae ab illo inventore veritatis et quasi architecto beatae vitae dicta...</p>
      <a class="btn btn-more" href="#">MORE</a>
    </article>
  </div>
</section>

<section class="section features">
  <div class="wrap features-grid">
    <article class="feature">
      <div class="thumb" role="img" aria-label="Speaker presenting to a conference audience" style="background:linear-gradient(135deg,#c96a3a,#3a3f6a 60%,#1f2440)"></div>
      <span class="feature-icon"><svg width="32" height="32" viewBox="0 0 32 32"><rect x="4" y="6" width="24" height="22" fill="none" stroke="#fff" stroke-width="2"/><path d="M4 12h24M10 3v6M22 3v6" stroke="#fff" stroke-width="2"/></svg></span>
      <h3>CONFERENCES &amp; EVENTS</h3>
      <p>Aperiam, eaque ipsa quae ab illo inventore verita quasi architecto beatae vitae dicta...</p>
      <a class="btn btn-more" href="#">MORE</a>
    </article>
    <article class="feature">
      <div class="thumb" role="img" aria-label="Friends toasting at a party dinner table" style="background:linear-gradient(135deg,#2a1c16,#8a5a36 55%,#3a2418)"></div>
      <span class="feature-icon"><svg width="32" height="32" viewBox="0 0 32 32"><path d="M9 5h6l-1 9a2 2 0 0 1-4 0zM17 5h6l-1 9a2 2 0 0 1-4 0zM12 16v10M20 16v10M9 27h6M17 27h6" fill="none" stroke="#fff" stroke-width="2"/></svg></span>
      <h3>PARTIES AT BRACKMOOR</h3>
      <p>Aperiam, eaque ipsa quae ab illo inventore verita quasi architecto beatae vitae dicta...</p>
      <a class="btn btn-more" href="#">MORE</a>
    </article>
    <article class="feature">
      <div class="thumb" role="img" aria-label="Glass globe resting on a keyboard" style="background:linear-gradient(135deg,#1c2f44,#5fb3e0 55%,#22384f)"></div>
      <span class="feature-icon"><svg width="32" height="32" viewBox="0 0 32 32"><rect x="5" y="7" width="22" height="15" fill="none" stroke="#fff" stroke-width="2"/><path d="M2 25h28" stroke="#fff" stroke-width="2"/></svg></span>
      <h3>CO-WORKING HUB</h3>
      <p>Aperiam, eaque ipsa quae ab illo inventore verita quasi architecto beatae vitae dicta...</p>
      <a class="btn btn-more" href="#">MORE</a>
    </article>
  </div>
</section>

<section class="section sports" role="img" aria-label="Fitness class exercising, tinted teal">
  <h2>SPORTS <b>&amp; LEISURE</b></h2>
  <a href="#">CLICK MORE INFORMATION</a>
</section>

<footer class="section site-footer">
  <div class="footer-logo"><span class="brand-mark"></span><span class="brand-name">BRACKMOOR<br>HALLS</span></div>
  <p class="copyright">©brackmoorhalls.2016 Privacy Policy</p>
  <span class="divider" style="left:425px"></span>
  <span class="divider" style="left:731px"></span>
  <div class="footer-col" style="left:490px">
    <h4>NAVIGATION</h4>
    <ul><li>Brackmoor Entertainment Venue</li><li>Harlow Close</li><li>Brackmoor</li><li>Wessex</li><li>BM4 2QT</li></ul>
  </div>
  <div class="footer-col" style="left:792px">
    <h4>NAVIGATION</h4>
    <ul><li>What's On</li><li>Conferencing &amp; Events</li><li>Sports &amp; Leisure</li><li>Lantern Theatre</li></ul>
  </div>
  <div class="footer-col extra" style="left:992px">
    <ul><li>Plan Your Visit</li><li>News</li><li>Discover More</li><li>Contact Us</li></ul>
  </div>
</footer>

</body>
</html>
```